Tech Company New PowerPoint Design Project

We are an IT Managed services, cloud and cyber security company https://www.travolin.com.au/ Requesting proposals for a PowerPoint deck template that can be used by our sales team when pitching clients, our head office is located in Australa and we do have regional offices in NZ , USA , SRI LANKA and SINGAPORE. and also required to have a proposal/SOW template created too (not sure if this is something that we can include to this proposal) we may need a lot of things done in future but this is where i like to get started for now.. please let m eknow your thoughts and if you have any questions.
Target Market(s)
Enterprise
Industry/Entity Type
Information Technology
Look and feel

```html
<!DOCTYPE html>
<html lang="en">
<head>
<meta charset="utf-8">
<title>Travolin Deck Overview</title>
<link href="https://fonts.googleapis.com/css2?family=Poppins:wght@300;400;500;600;700&family=Roboto+Condensed:wght@400;700&display=swap" rel="stylesheet">
<style>
:root{
  --navy:#1c2540;
  --navy-2:#263253;
  --cyan:#29b5ec;
  --white:#ffffff;
  --ink:#2a2f3d;
  --grey-text:#6f7481;
  --light-text:#c4ccdc;
  --backdrop:#8d9095;
}
*{box-sizing:border-box;margin:0;padding:0}
html,body{width:786px;height:1200px;overflow:hidden;background:var(--backdrop)}
body{font-family:'Poppins',sans-serif;color:var(--ink)}
.deck{position:absolute;left:23px;top:32px;display:grid;grid-template-columns:repeat(3,240px);grid-auto-rows:135px;column-gap:9px;row-gap:7px}
.slide{position:relative;background:var(--white);overflow:hidden;box-shadow:0 2px 5px rgba(0,0,0,.35)}
.abs{position:absolute}
.logo{position:absolute;top:5px;right:8px;font:300 8px 'Poppins',sans-serif;color:var(--cyan)}
.title{position:absolute;font:700 9px 'Roboto Condensed',sans-serif;color:var(--navy);white-space:nowrap}
.title::after{content:"";display:block;width:14px;height:1px;background:var(--cyan);margin-top:2px}
.title.light{color:var(--white)}
.tx{position:absolute;font:400 3px/1.4 'Poppins',sans-serif;color:var(--grey-text);text-align:justify}
.tx.light{color:var(--light-text)}
.tx.xs{font-size:2.6px}
.tx.c{text-align:center}
.head{position:absolute;font:600 4px 'Poppins',sans-serif;color:var(--navy);white-space:nowrap}
.head.cyan{color:var(--cyan)}
.head.light{color:var(--white)}
.foot{position:absolute;left:0;bottom:5px;display:flex;align-items:center;font:400 2.8px 'Poppins',sans-serif;letter-spacing:.6px;color:var(--navy)}
.foot b{background:var(--cyan);color:var(--white);font-weight:600;padding:0 3px 0 5px;margin-right:2px}
.foot.light{color:var(--white)}
.pg{position:absolute;right:5px;bottom:4px;width:4px;height:4px;background:var(--cyan)}
.panel{position:absolute;background:var(--navy)}
.photo{position:absolute}
.num{position:absolute;width:10px;height:10px;border-radius:50%;background:var(--cyan);color:var(--white);font:700 5px/10px 'Poppins',sans-serif;text-align:center}
.dots{position:absolute;font:700 6px 'Poppins',sans-serif;color:var(--cyan);letter-spacing:.8px}
.icon-circ{position:absolute;width:12px;height:12px;border-radius:50%;border:1px solid var(--cyan);background:var(--white)}
.toc{position:absolute;width:90px}
.toc .h{font:600 5px 'Poppins',sans-serif;color:var(--navy)}
.toc .h span{color:var(--cyan);margin-right:4px}
.toc .tx{position:static;margin:1px 0 0 10px;width:78px;text-align:left}
</style>
</head>
<body>
<main class="deck">

<!-- 1 cover -->
<section class="slide" style="background:var(--navy)">
  <div class="photo" style="inset:0;background:linear-gradient(180deg,#1f3256 0%,#2c4d7c 38%,#142343 62%,#0c1429 100%)" role="img" aria-label="Harbour bridge skyline at dusk"></div>
  <div class="abs" style="left:6px;top:5px;width:6px;height:6px;background:var(--cyan)"></div>
  <div class="abs" style="left:63px;top:52px;font:300 26px 'Poppins',sans-serif;color:var(--cyan)">travolin</div>
  <div class="abs" style="left:64px;top:87px;right:0;height:9px;background:var(--cyan);font:600 6.5px/9px 'Poppins',sans-serif;color:var(--navy);padding-left:4px">BUSINESS MARKETING MARKETING</div>
</section>

<!-- 2 cover -->
<section class="slide">
  <div class="photo" style="inset:0;background:linear-gradient(100deg,#0e1628 28%,#3b4e70 58%,#8e9cb2 80%,#c9d1dc)" role="img" aria-label="Hands working on a laptop"></div>
  <div class="abs" style="left:12px;top:12px;font:300 22px 'Poppins',sans-serif;color:var(--cyan)">travolin</div>
  <div class="abs" style="left:12px;top:72px;font:400 6px 'Poppins',sans-serif;color:var(--white)">PRESENTATION</div>
  <div class="abs" style="left:12px;top:79px;font:700 17px/1 'Roboto Condensed',sans-serif;color:var(--cyan)">BUSINESS</div>
  <div class="abs" style="left:12px;top:97px;font:700 13px/1 'Roboto Condensed',sans-serif;color:var(--white)">MARKETING</div>
  <div class="abs" style="left:12px;top:118px;font:400 4px 'Poppins',sans-serif;color:var(--white);letter-spacing:1px">www.travolin.com.au</div>
  <div class="abs" style="left:90px;top:121px;width:150px;height:.6px;background:var(--cyan)"></div>
</section>

<!-- 3 contents -->
<section class="slide">
  <div class="logo">travolin</div>
  <div class="abs" style="left:17px;top:12px;font:700 10px 'Roboto Condensed',sans-serif;color:#3b3b3b">Contents</div>
  <div class="toc" style="left:24px;top:36px"><div class="h"><span>1.</span>Lorem ipsum</div><p class="tx">Managed support and secure cloud for growing enterprise teams.</p></div>
  <div class="toc" style="left:124px;top:36px"><div class="h"><span>2.</span>Lorem ipsum</div><p class="tx">Managed support and secure cloud for growing enterprise teams.</p></div>
  <div class="toc" style="left:24px;top:63px"><div class="h"><span>3.</span>Lorem ipsum</div><p class="tx">Managed support and secure cloud for growing enterprise teams.</p></div>
  <div class="toc" style="left:124px;top:63px"><div class="h"><span>4.</span>Lorem ipsum</div><p class="tx">Managed support and secure cloud for growing enterprise teams.</p></div>
  <div class="toc" style="left:24px;top:90px"><div class="h"><span>5.</span>Lorem ipsum</div><p class="tx">Managed support and secure cloud for growing enterprise teams.</p></div>
  <div class="toc" style="left:124px;top:90px"><div class="h"><span>6.</span>Lorem ipsum</div><p class="tx">Managed support and secure cloud for growing enterprise teams.</p></div>
  <div class="foot"><b>www</b>travolin.com.au</div><div class="pg"></div>
</section>

<!-- 4 agenda -->
<section class="slide">
  <div class="panel" style="left:0;top:0;width:72px;bottom:0"></div>
  <div class="title light" style="left:8px;top:8px">Agenda</div>
  <p class="tx light" style="left:8px;top:31px;width:56px">Secure cloud and managed services for enterprise teams across Australia and the region. We plan, migrate and protect critical systems so your people can focus on growth.</p>
  <p class="tx light" style="left:8px;top:68px;width:56px">Our engineers watch networks around the clock and respond fast. We plan, migrate and protect critical systems so your people can focus on growth and new work.</p>
  <div class="logo">travolin</div>
  <div class="num" style="left:86px;top:32px;border-radius:2px;transform:rotate(45deg)"><span style="display:block;transform:rotate(-45deg)">1</span></div>
  <div class="head" style="left:100px;top:31px">Lorem ipsum</div><p class="tx" style="left:100px;top:37px;width:42px">Managed support and secure cloud for growing enterprise teams.</p>
  <div class="num" style="left:86px;top:61px;border-radius:2px;transform:rotate(45deg)"><span style="display:block;transform:rotate(-45deg)">2</span></div>
  <div class="head" style="left:100px;top:60px">Lorem ipsum</div><p class="tx" style="left:100px;top:66px;width:42px">Managed support and secure cloud for growing enterprise teams.</p>
  <div class="num" style="left:86px;top:90px;border-radius:2px;transform:rotate(45deg)"><span style="display:block;transform:rotate(-45deg)">3</span></div>
  <div class="head" style="left:100px;top:89px">Lorem ipsum</div><p class="tx" style="left:100px;top:95px;width:42px">Managed support and secure cloud for growing enterprise teams.</p>
  <div class="num" style="left:153px;top:32px;border-radius:2px;transform:rotate(45deg)"><span style="display:block;transform:rotate(-45deg)">4</span></div>
  <div class="head" style="left:167px;top:31px">Lorem ipsum</div><p class="tx" style="left:167px;top:37px;width:42px">Managed support and secure cloud for growing enterprise teams.</p>
  <div class="num" style="left:153px;top:61px;border-radius:2px;transform:rotate(45deg)"><span style="display:block;transform:rotate(-45deg)">5</span></div>
  <div class="head" style="left:167px;top:60px">Lorem ipsum</div><p class="tx" style="left:167px;top:66px;width:42px">Managed support and secure cloud for growing enterprise teams.</p>
  <div class="num" style="left:153px;top:90px;border-radius:2px;transform:rotate(45deg)"><span style="display:block;transform:rotate(-45deg)">6</span></div>
  <div class="head" style="left:167px;top:89px">Lorem ipsum</div><p class="tx" style="left:167px;top:95px;width:42px">Managed support and secure cloud for growing enterprise teams.</p>
  <div class="foot light"><b>www</b>travolin.com.au</div><div class="pg"></div>
</section>

<!-- 5 about us -->
<section class="slide">
  <div class="panel" style="left:0;top:0;width:95px;height:24px"></div>
  <div class="title light" style="left:10px;top:7px">About Us</div>
  <div class="logo">travolin</div>
  <div class="abs" style="left:10px;top:30px;font:500 7px/1.15 'Poppins',sans-serif;color:var(--navy)">Lorem Ipsum<br>Dolor Sit Ametkeeper.</div>
  <p class="tx" style="left:10px;top:49px;width:90px">Secure cloud and managed services for enterprise teams across Australia and the region. We plan, migrate and protect critical systems so your people can focus on growth. Our engineers watch networks around the clock and respond fast.</p>
  <p class="tx" style="left:10px;top:78px;width:90px">Secure cloud and managed services for enterprise teams across Australia and the region. We plan, migrate and protect critical systems so your people can focus on growth. Our engineers watch networks around the clock and respond fast.</p>
  <div class="panel" style="left:155px;top:77px;width:85px;height:58px"></div>
  <div class="photo" style="left:104px;top:21px;width:100px;height:97px;background:linear-gradient(135deg,#e4eaf1,#a7b6c9 45%,#4f6080 85%,#2d3a55)" role="img" aria-label="Hands typing on a laptop keyboard"></div>
  <div class="dots" style="left:190px;top:24px;font-size:5px">::::</div>
  <div class="foot"><b>www</b>travolin.com.au</div><div class="pg"></div>
</section>

<!-- 6 company about -->
<section class="slide">
  <div class="title" style="left:7px;top:6px">Company About</div>
  <div class="logo">travolin</div>
  <div class="panel" style="left:14px;top:27px;width:123px;height:85px"></div>
  <p class="tx light" style="left:21px;top:32px;width:106px">Secure cloud and managed services for enterprise teams across Australia and the region. We plan, migrate and protect critical systems so your people can focus on growth. Our engineers watch networks around the clock and respond fast. Secure cloud and managed services for enterprise teams across Australia and the region. We plan, migrate and protect critical systems.</p>
  <p class="tx light" style="left:21px;top:73px;width:106px">Our engineers watch networks around the clock and respond fast. Secure cloud and managed services for enterprise teams across Australia and the region. We plan, migrate and protect critical systems so your people can focus on growth and new work every day.</p>
  <div class="icon-circ" style="left:130px;top:32px;width:15px;height:15px;background:var(--cyan);border:1.5px solid var(--white)"></div>
  <div class="head cyan" style="left:149px;top:32px">Lorem ipsum</div><p class="tx" style="left:149px;top:38px;width:78px;text-align:left">Managed support and secure cloud for growing enterprise teams.</p>
  <div class="icon-circ" style="left:130px;top:62px;width:15px;height:15px;background:var(--cyan);border:1.5px solid var(--white)"></div>
  <div class="head cyan" style="left:149px;top:62px">Lorem ipsum</div><p class="tx" style="left:149px;top:68px;width:78px;text-align:left">Managed support and secure cloud for growing enterprise teams.</p>
  <div class="icon-circ" style="left:130px;top:94px;width:15px;height:15px;background:var(--cyan);border:1.5px solid var(--white)"></div>
  <div class="head cyan" style="left:149px;top:94px">Lorem ipsum</div><p class="tx" style="left:149px;top:100px;width:78px;text-align:left">Managed support and secure cloud for growing enterprise teams.</p>
  <div class="foot"><b>www</b>travolin.com.au</div><div class="pg"></div>
</section>

<!-- 7 founder -->
<section class="slide">
  <div class="title" style="left:10px;top:10px">Founder Profile</div>
  <div class="panel" style="left:193px;top:0;width:47px;height:30px"></div>
  <div class="logo">travolin</div>
  <div class="dots" style="left:136px;top:6px">:::::</div>
  <p class="tx" style="left:10px;top:30px;width:58px">Secure cloud and managed services for enterprise teams across Australia and the region. We plan, migrate and protect critical systems so your people can focus on growth. Our engineers watch networks around the clock and respond fast.</p>
  <p class="tx" style="left:75px;top:30px;width:58px">Secure cloud and managed services for enterprise teams across Australia and the region. We plan, migrate and protect critical systems so your people can focus on growth. Our engineers watch networks around the clock and respond fast.</p>
  <p class="tx" style="left:10px;top:72px;width:58px">Secure cloud and managed services for enterprise teams across Australia and the region. We plan, migrate and protect critical systems so your people can focus on growth. Our engineers watch networks around the clock and respond fast.</p>
  <p class="tx" style="left:75px;top:72px;width:58px">Secure cloud and managed services for enterprise teams across Australia and the region. We plan, migrate and protect critical systems so your people can focus on growth. Our engineers watch networks around the clock and respond fast.</p>
  <div class="photo" style="left:140px;top:18px;width:80px;height:105px;background:linear-gradient(160deg,#9fb0c6,#4e6585 45%,#1e2b46 90%)" role="img" aria-label="Two colleagues reviewing a laptop in a server room"></div>
  <div class="foot"><b>www</b>travolin.com.au</div><div class="pg"></div>
</section>

<!-- 8 education -->
<section class="slide">
  <div class="title" style="left:7px;top:6px">Our Company Education</div>
  <div class="logo">travolin</div>
  <div class="abs" style="left:20px;top:28px;width:200px;height:60px;background:radial-gradient(ellipse at center,#e8ecf2,#fff 70%)" role="img" aria-label="Faint world map"></div>
  <svg class="abs" style="left:40px;top:30px" width="160" height="65" viewBox="0 0 160 65" fill="none" stroke="#1c2540" stroke-width="1.4">
    <rect x="4" y="2" width="40" height="60" rx="6"/>
    <rect x="60" y="2" width="40" height="60" rx="6"/>
    <rect x="116" y="2" width="40" height="60" rx="6"/>
    <path d="M44 18 H52 Q56 18 56 14 V8 Q56 2 60 2"/>
    <path d="M100 18 H108 Q112 18 112 14 V8 Q112 2 116 2"/>
    <circle cx="44" cy="18" r="1.8" fill="#1c2540"/>
    <circle cx="100" cy="18" r="1.8" fill="#1c2540"/>
    <g stroke="#29b5ec" stroke-width=".8"><circle cx="24" cy="14" r="3"/><rect x="76" y="11" width="8" height="6"/><path d="M76 11 L80 14 L84 11 M132 18 H140 M132 18 V10 M133 17 L139 11"/></g>
  </svg>
  <div class="head cyan" style="left:44px;top:54px;width:40px;text-align:center;font-size:3.6px">IDEA</div>
  <div class="head cyan" style="left:100px;top:54px;width:40px;text-align:center;font-size:3.6px">PROMOTION</div>
  <div class="head cyan" style="left:156px;top:54px;width:40px;text-align:center;font-size:3.6px">GROWTH</div>
  <p class="tx xs c" style="left:47px;top:60px;width:34px">Managed support and secure cloud for growing enterprise teams.</p>
  <p class="tx xs c" style="left:103px;top:60px;width:34px">Managed support and secure cloud for growing enterprise teams.</p>
  <p class="tx xs c" style="left:159px;top:60px;width:34px">Managed support and secure cloud for growing enterprise teams.</p>
  <p class="tx c" style="left:28px;top:100px;width:184px">Secure cloud and managed services for enterprise teams across Australia and the region. We plan, migrate and protect critical systems so your people can focus on growth. Our engineers watch networks around the clock and respond fast.</p>
  <div class="foot"><b>www</b>travolin.com.au</div><div class="pg"></div>
</section>

<!-- 9 text here chart -->
<section class="slide">
  <div class="panel" style="left:0;top:0;width:85px;bottom:0"></div>
  <div class="title light" style="left:7px;top:6px">Text Here</div>
  <p class="tx light" style="left:7px;top:25px;width:66px">Secure cloud and managed services for enterprise teams across Australia and the region. We plan, migrate and protect critical systems so your people can focus on growth. Our engineers watch networks around the clock and respond fast.</p>
  <p class="tx light" style="left:7px;top:76px;width:66px">Secure cloud and managed services for enterprise teams across Australia and the region. We plan, migrate and protect critical systems so your people can focus on growth. Our engineers watch networks around the clock and respond fast.</p>
  <div class="logo">travolin</div>
  <div class="abs" style="left:98px;top:21px;font:500 3.6px 'Poppins',sans-serif;color:var(--navy)">CONSECTETUER ADIPISCING</div>
  <svg class="abs" style="left:92px;top:29px" width="142" height="65" viewBox="0 0 142 65" font-family="Poppins,sans-serif" font-size="3.4" fill="#2a2f3d">
    <g stroke="#e3e6ec" stroke-width=".4"><path d="M10 2H138M10 11H138M10 20H138M10 29H138M10 38H138M10 47H138M10 56H138"/><path d="M138 2V56"/></g>
    <text x="2" y="3">60</text><text x="2" y="12">50</text><text x="2" y="21">40</text><text x="2" y="30">30</text><text x="2" y="39">20</text><text x="2" y="48">10</text><text x="5" y="57">0</text>
    <rect x="20" y="9" width="13" height="47" fill="#29b5ec"/>
    <rect x="45" y="27" width="13" height="29" fill="#1c2540"/>
    <rect x="70" y="14" width="13" height="42" fill="#29b5ec"/>
    <rect x="95" y="31" width="13" height="25" fill="#1c2540"/>
    <text x="22" y="63">JAN</text><text x="47" y="63">FEB</text><text x="72" y="63">MAR</text><text x="97" y="63">APR</text>
  </svg>
  <div class="abs" style="left:96px;top:103px;width:4px;height:4px;border-radius:50%;background:var(--cyan)"></div>
  <div class="head" style="left:102px;top:102px">Lorem ipsum</div><p class="tx" style="left:102px;top:108px;width:48px;text-align:left">Managed support and secure cloud for growing enterprise teams.</p>
  <div class="abs" style="left:162px;top:103px;width:4px;height:4px;border-radius:50%;background:var(--cyan)"></div>
  <div class="head" style="left:168px;top:102px">Lorem ipsum</div><p class="tx" style="left:168px;top:108px;width:48px;text-align:left">Managed support and secure cloud for growing enterprise teams.</p>
  <div class="foot light"><b>www</b>travolin.com.au</div><div class="pg"></div>
</section>

<!-- 10 overview -->
<section class="slide">
  <div class="panel" style="left:0;top:0;width:115px;height:60px"></div>
  <div class="title light" style="left:7px;top:6px">Company Overview</div>
  <p class="tx light" style="left:7px;top:22px;width:102px">Secure cloud and managed services for enterprise teams across Australia and the region. We plan, migrate and protect critical systems so your people can focus on growth. Our engineers watch networks around the clock and respond fast.</p>
  <p class="tx light" style="left:7px;top:45px;width:102px">Managed support and secure cloud for growing enterprise teams.</p>
  <div class="logo">travolin</div>
  <svg class="abs" style="left:124px;top:20px" width="112" height="60" viewBox="0 0 112 60" font-family="Poppins,sans-serif" font-size="3" fill="#2a2f3d">
    <g stroke="#e3e6ec" stroke-width=".4"><path d="M9 2H110M9 10H110M9 18H110M9 26H110M9 34H110M9 42H110M9 50H110"/></g>
    <text x="0" y="3">60</text><text x="0" y="11">50</text><text x="0" y="19">40</text><text x="0" y="27">30</text><text x="0" y="35">20</text><text x="0" y="43">10</text><text x="3" y="51">0</text>
    <rect x="17" y="10" width="3" height="40" fill="#29b5ec"/><rect x="22" y="8" width="3" height="42" fill="#1c2540"/>
    <rect x="38" y="41" width="3" height="9" fill="#1c2540"/><rect x="43" y="21" width="3" height="29" fill="#29b5ec"/>
    <rect x="59" y="5" width="3" height="45" fill="#1c2540"/><rect x="64" y="33" width="3" height="17" fill="#29b5ec"/>
    <rect x="80" y="8" width="3" height="42" fill="#29b5ec"/><rect x="85" y="26" width="3" height="24" fill="#1c2540"/>
    <text x="19" y="57">JAN</text><text x="40" y="57">FEB</text><text x="61" y="57">MAR</text><text x="82" y="57">APR</text>
  </svg>
  <svg class="abs" style="left:5px;top:69px" width="112" height="50" viewBox="0 0 112 50" font-family="Poppins,sans-serif" font-size="2.2" fill="#2a2f3d">
    <g stroke="#e3e6ec" stroke-width=".4"><path d="M8 2H108M8 8H108M8 14H108M8 20H108M8 26H108M8 32H108M8 38H108"/></g>
    <text x="0" y="3">60</text><text x="0" y="9">50</text><text x="0" y="15">40</text><text x="0" y="21">30</text><text x="0" y="27">20</text><text x="0" y="33">10</text><text x="2" y="39">0</text>
    <polyline points="14,32 26,36 36,28 48,10 58,20 70,14 82,22 94,16 104,34" fill="none" stroke="#1c2540" stroke-width=".6"/>
    <polyline points="14,34 26,30 36,20 48,22 58,26 70,18 82,28 94,22 104,18" fill="none" stroke="#29b5ec" stroke-width=".6"/>
    <text x="12" y="44">TEXT 01</text><text x="34" y="44">TEXT 03</text><text x="56" y="44">TEXT 05</text><text x="78" y="44">TEXT 07</text><text x="98" y="44">TEXT 09</text>
  </svg>
  <div class="head cyan" style="left:128px;top:84px;font-size:3.4px">Lorem ipsum</div><p class="tx" style="left:128px;top:89px;width:44px;text-align:left">Managed support and secure cloud for growing enterprise teams.</p>
  <div class="head" style="left:186px;top:84px;font-size:3.4px">Lorem ipsum</div><p class="tx" style="left:186px;top:89px;width:44px;text-align:left">Managed support and secure cloud for growing enterprise teams.</p>
  <div class="head" style="left:128px;top:102px;font-size:3.4px">Lorem ipsum</div><p class="tx" style="left:128px;top:107px;width:44px;text-align:left">Managed support and secure cloud for growing enterprise teams.</p>
  <div class="head cyan" style="left:186px;top:102px;font-size:3.4px">Lorem ipsum</div><p class="tx" style="left:186px;top:107px;width:44px;text-align:left">Managed support and secure cloud for growing enterprise teams.</p>
  <div class="foot"><b>www</b>travolin.com.au</div><div class="pg"></div>
</section>

<!-- 11 lorem ipsum two columns -->
<section class="slide">
  <div class="logo">travolin</div>
  <div class="panel" style="left:15px;top:12px;width:105px;height:104px"></div>
  <div class="abs" style="left:22px;top:17px;font:500 6.5px/1.1 'Poppins',sans-serif;color:var(--white)">LOREM IPSUM<br><b style="color:var(--cyan)">DOLOR SIT AMET</b></div>
  <p class="tx light" style="left:22px;top:33px;width:92px">Secure cloud and managed services for enterprise teams across Australia and the region. We plan, migrate and protect critical systems so your people can focus on growth. Our engineers watch networks around the clock and respond fast.</p>
  <p class="tx light" style="left:22px;top:58px;width:92px">Secure cloud and managed services for enterprise teams across Australia and the region. We plan, migrate and protect critical systems so your people can focus on growth. Our engineers watch networks around the clock and respond fast.</p>
  <p class="tx light" style="left:22px;top:87px;width:92px;text-align:left">▸ Managed support and secure cloud for growing enterprise teams.</p>
  <p class="tx light" style="left:22px;top:100px;width:92px;text-align:left">▹ Managed support and secure cloud for growing enterprise teams.</p>
  <div class="abs" style="left:130px;top:17px;font:500 6.5px/1.1 'Poppins',sans-serif;color:var(--cyan)">LOREM IPSUM<br><b style="color:var(--navy)">DOLOR SIT AMET</b></div>
  <p class="tx" style="left:130px;top:33px;width:95px">Secure cloud and managed services for enterprise teams across Australia and the region. We plan, migrate and protect critical systems so your people can focus on growth. Our engineers watch networks around the clock and respond fast.</p>
  <p class="tx" style="left:130px;top:58px;width:95px">Secure cloud and managed services for enterprise teams across Australia and the region. We plan, migrate and protect critical systems so your people can focus on growth. Our engineers watch networks around the clock and respond fast.</p>
  <p class="tx" style="left:130px;top:87px;width:90px;text-align:left">▸ Managed support and secure cloud for growing enterprise teams.</p>
  <p class="tx" style="left:130px;top:100px;width:90px;text-align:left">▹ Managed support and secure cloud for growing enterprise teams.</p>
  <div class="foot"><b>www</b>travolin.com.au</div><div class="pg"></div>
</section>

<!-- 12 active intelligence -->
<section class="slide">
  <div class="title" style="left:12px;top:9px">Active Intelligence</div>
  <div class="logo">travolin</div>
  <div class="abs" style="left:168px;top:22px;width:55px;height:1.5px;background:var(--cyan)"></div>
  <p class="tx" style="left:11px;top:28px;width:94px">Secure cloud and managed services for enterprise teams across Australia and the region. We plan, migrate and protect critical systems so your people can focus on growth. Our engineers watch networks around the clock and respond fast.</p>
  <p class="tx" style="left:11px;top:56px;width:94px">Secure cloud and managed services for enterprise teams across Australia and the region. We plan, migrate and protect critical systems so your people can focus on growth. Our engineers watch networks around the clock and respond fast.</p>
  <p class="tx" style="left:11px;top:87px;width:92px;text-align:left">▸ Managed support and secure cloud for growing enterprise teams.</p>
  <p class="tx" style="left:11px;top:100px;width:92px;text-align:left">▹ Managed support and secure cloud for growing enterprise teams.</p>
  <div class="abs" style="left:116px;top:62px;width:2px;height:53px;background:var(--cyan)"></div>
  <div class="abs" style="left:116px;top:113px;width:60px;height:2px;background:var(--cyan)"></div>
  <div class="photo" style="left:118px;top:25px;width:122px;height:88px;background:linear-gradient(160deg,#d6e1ec,#7890b0 40%,#34486b 75%,#9a7a52)" role="img" aria-label="Glass office towers seen from below"></div>
  <div class="foot"><b>www</b>travolin.com.au</div><div class="pg"></div>
</section>

<!-- 13 services -->
<section class="slide">
  <div class="title" style="left:7px;top:5px">Text Here</div>
  <div class="panel" style="left:70px;top:0;right:0;bottom:0"></div>
  <div class="logo">travolin</div>
  <div class="dots" style="left:79px;top:12px;line-height:2.5px;font-size:4px">:<br>:<br>:</div>
  <div class="photo" style="left:19px;top:24px;width:80px;height:95px;background:linear-gradient(160deg,#0c1630,#143a63 45%,#1f78aa 75%,#2ab6ec)" role="img" aria-label="Abstract blue technology backdrop"></div>
  <div class="abs" style="left:25px;top:55px;font:300 15px/1.1 'Roboto Condensed',sans-serif;color:var(--white)">ABOUT<br>OUR<br><b style="font-weight:700">SERVICES</b></div>
  <div class="num" style="left:105px;top:30px;width:14px;height:14px;line-height:14px;font-size:7px">1</div>
  <p class="tx light" style="left:125px;top:29px;width:102px">Secure cloud and managed services for enterprise teams, with round-the-clock monitoring and fast local support.</p>
  <div class="num" style="left:105px;top:63px;width:14px;height:14px;line-height:14px;font-size:7px">2</div>
  <p class="tx light" style="left:125px;top:60px;width:102px">Secure cloud and managed services for enterprise teams, with round-the-clock monitoring and fast local support.</p>
  <div class="num" style="left:105px;top:97px;width:14px;height:14px;line-height:14px;font-size:7px">3</div>
  <p class="tx light" style="left:125px;top:96px;width:102px">Secure cloud and managed services for enterprise teams, with round-the-clock monitoring and fast local support.</p>
  <div class="foot"><b>www</b>travolin.com.au</div><div class="pg"></div>
</section>

<!-- 14 our value -->
<section class="slide">
  <div class="title" style="left:7px;top:5px">Our Value</div>
  <div class="logo">travolin</div>
  <div class="num" style="left:25px;top:40px;width:16px;height:16px;line-height:16px;font-size:8px;border:1.5px solid var(--white);box-shadow:0 0 0 .6px var(--cyan)">1</div>
  <div class="abs" style="left:47px;top:42px;font:600 10px/1.1 'Poppins',sans-serif;color:var(--navy)">Lorem<br>ipsum dolor<br>sit amet</div>
  <div class="abs" style="left:47px;top:80px;width:60px;font:400 4px/1.2 'Poppins',sans-serif;color:var(--grey-text)">Praesent bibendum at risus ac blandit. In eu risus vel felis elementum venenatis vitae sed lacus. Curabitur vel erat urna.</div>
  <div class="panel" style="left:125px;top:33px;width:83px;height:73px"></div>
  <div class="num" style="left:117px;top:40px;width:16px;height:16px;line-height:16px;font-size:8px;border:1.5px solid var(--white)">2</div>
  <div class="abs" style="left:139px;top:41px;font:600 10px/1.1 'Poppins',sans-serif;color:var(--cyan)">Lorem<br>ipsum dolor<br>sit amet</div>
  <div class="abs" style="left:139px;top:79px;width:64px;font:400 4px/1.2 'Poppins',sans-serif;color:var(--white)">Praesent bibendum at risus ac blandit. In eu risus vel felis elementum venenatis vitae sed lacus. Curabitur vel erat urna.</div>
  <div class="foot"><b>www</b>travolin.com.au</div><div class="pg"></div>
</section>

<!-- 15 our story -->
<section class="slide">
  <div class="title" style="left:10px;top:8px">Our Story</div>
  <div class="photo" style="left:99px;top:0;width:141px;height:60px;background:linear-gradient(120deg,#a9b6c6,#e1e6ec 40%,#7587a1 75%,#3b4a66)" role="img" aria-label="Team meeting in a high-rise office"></div>
  <div class="dots" style="left:85px;top:35px;font-size:5px">::::::</div>
  <div class="panel" style="left:0;top:60px;width:98px;height:57px"></div>
  <p class="tx light" style="left:10px;top:67px;width:82px">Secure cloud and managed services for enterprise teams across Australia and the region. We plan, migrate and protect critical systems so your people can focus on growth. Our engineers watch networks around the clock and respond fast.</p>
  <p class="tx light" style="left:10px;top:101px;width:82px">Managed support and secure cloud for growing enterprise teams.</p>
  <p class="tx" style="left:110px;top:65px;width:56px">Secure cloud and managed services for enterprise teams across Australia and the region. We plan, migrate and protect critical systems so your people can focus on growth. Our engineers watch networks around the clock and respond fast.</p>
  <p class="tx" style="left:172px;top:65px;width:56px">Secure cloud and managed services for enterprise teams across Australia and the region. We plan, migrate and protect critical systems so your people can focus on growth. Our engineers watch networks around the clock and respond fast.</p>
  <div class="foot"><b>www</b>travolin.com.au</div><div class="pg"></div>
</section>

<!-- 16 domain -->
<section class="slide">
  <div class="title" style="left:17px;top:12px">What's A Domain?</div>
  <div class="logo">travolin</div>
  <p class="tx" style="left:16px;top:35px;width:96px">Secure cloud and managed services for enterprise teams across Australia and the region. We plan, migrate and protect critical systems so your people can focus on growth. Our engineers watch networks around the clock and respond fast.</p>
  <p class="tx" style="left:16px;top:63px;width:96px">Secure cloud and managed services for enterprise teams across Australia and the region. We plan, migrate and protect critical systems so your people can focus on growth. Our engineers watch networks around the clock and respond fast.</p>
  <p class="tx" style="left:16px;top:91px;width:96px">Secure cloud and managed services for enterprise teams across Australia and the region. We plan, migrate and protect critical systems so your people can focus on growth. Our engineers watch networks around the clock and respond fast.</p>
  <div class="panel" style="left:119px;top:36px;width:121px;height:77px"></div>
  <ul class="abs" style="left:126px;top:43px;list-style:none;font:300 5.2px/11px 'Poppins',sans-serif;color:var(--white)">
    <li><span style="color:var(--cyan)">▪</span>&nbsp; Fits your business or products</li>
    <li><span style="color:var(--cyan)">▪</span>&nbsp; Is easy to spell and remember</li>
    <li><span style="color:var(--cyan)">▪</span>&nbsp; Fits your business or products</li>
    <li><span style="color:var(--cyan)">▪</span>&nbsp; Is easy to spell and remember</li>
    <li><span style="color:var(--cyan)">▪</span>&nbsp; Fits your business or products</li>
    <li><span style="color:var(--cyan)">▪</span>&nbsp; Is easy to spell and remember</li>
  </ul>
  <div class="foot"><b>www</b>travolin.com.au</div><div class="pg"></div>
</section>

<!-- 17 subtitle text -->
<section class="slide">
  <div class="panel" style="left:0;top:0;right:0;height:48px"></div>
  <div class="title light" style="left:10px;top:7px">Subtitle Text</div>
  <div class="logo">travolin</div>
  <div class="dots" style="left:153px;top:21px;font-size:5px">:::::</div>
  <div class="photo" style="left:15px;top:34px;width:201px;height:62px;background:linear-gradient(110deg,#c7ced8,#eef0f3 35%,#9aa6b8 65%,#4b5a75)" role="img" aria-label="Colleagues working at office desks"></div>
  <div class="abs" style="left:21px;top:92px;width:11px;height:9px;background:var(--cyan);font:700 5px/9px 'Roboto Condensed',sans-serif;color:var(--navy);text-align:center">01</div>
  <p class="tx" style="left:38px;top:97px;width:44px;text-align:left">Managed support and secure cloud for growing enterprise teams.</p>
  <div class="abs" style="left:91px;top:92px;width:11px;height:9px;background:var(--cyan);font:700 5px/9px 'Roboto Condensed',sans-serif;color:var(--navy);text-align:center">02</div>
  <p class="tx" style="left:108px;top:97px;width:44px;text-align:left">Managed support and secure cloud for growing enterprise teams.</p>
  <div class="abs" style="left:161px;top:92px;width:11px;height:9px;background:var(--cyan);font:700 5px/9px 'Roboto Condensed',sans-serif;color:var(--navy);text-align:center">03</div>
  <p class="tx" style="left:178px;top:97px;width:44px;text-align:left">Managed support and secure cloud for growing enterprise teams.</p>
  <div class="foot"><b>www</b>travolin.com.au</div><div class="pg"></div>
</section>

<!-- 18 our text -->
<section class="slide">
  <div class="panel" style="left:0;top:0;width:78px;bottom:0"></div>
  <div class="title light" style="left:10px;top:7px">Our Text</div>
  <p class="tx light" style="left:12px;top:27px;width:60px">Secure cloud and managed services for enterprise teams, with round-the-clock monitoring and fast local support.</p>
  <p class="tx light" style="left:12px;top:49px;width:60px">Secure cloud and managed services for enterprise teams, with round-the-clock monitoring and fast local support.</p>
  <p class="tx light" style="left:12px;top:78px;width:60px">Secure cloud and managed services for enterprise teams, with round-the-clock monitoring and fast local support.</p>
  <div class="logo">travolin</div>
  <div class="abs" style="left:88px;top:25px;width:145px;height:90px;background:radial-gradient(ellipse at center,#e8ecf2,#fff 70%)" role="img" aria-label="Faint world map"></div>
  <div class="icon-circ" style="left:111px;top:25px;width:18px;height:18px"></div>
  <div class="head" style="left:96px;top:47px;width:48px;text-align:center;font-size:3.4px">LOREM IPSUM</div><p class="tx xs c" style="left:96px;top:52px;width:48px">Managed support and secure cloud for growing enterprise teams.</p>
  <div class="icon-circ" style="left:182px;top:25px;width:18px;height:18px"></div>
  <div class="head" style="left:167px;top:47px;width:48px;text-align:center;font-size:3.4px">LOREM IPSUM</div><p class="tx xs c" style="left:167px;top:52px;width:48px">Managed support and secure cloud for growing enterprise teams.</p>
  <div class="icon-circ" style="left:111px;top:75px;width:18px;height:18px"></div>
  <div class="head" style="left:96px;top:97px;width:48px;text-align:center;font-size:3.4px">LOREM IPSUM</div><p class="tx xs c" style="left:96px;top:102px;width:48px">Managed support and secure cloud for growing enterprise teams.</p>
  <div class="icon-circ" style="left:182px;top:75px;width:18px;height:18px"></div>
  <div class="head" style="left:167px;top:97px;width:48px;text-align:center;font-size:3.4px">LOREM IPSUM</div><p class="tx xs c" style="left:167px;top:102px;width:48px">Managed support and secure cloud for growing enterprise teams.</p>
  <div class="foot light"><b>www</b>travolin.com.au</div><div class="pg"></div>
</section>

<!-- 19 roadmap -->
<section class="slide">
  <div class="panel" style="left:0;top:0;width:72px;bottom:0"></div>
  <div class="title light" style="left:7px;top:7px">Roadmap</div>
  <div class="num" style="left:9px;top:29px;width:12px;height:12px;line-height:12px;font-size:6px;border:1px solid var(--white)">A</div>
  <div class="head light" style="left:26px;top:29px">2019</div><p class="tx light xs" style="left:26px;top:35px;width:42px;text-align:left">Managed support and secure cloud for growing enterprise teams.</p>
  <div class="num" style="left:9px;top:56px;width:12px;height:12px;line-height:12px;font-size:6px;border:1px solid var(--white)">B</div>
  <div class="head light" style="left:26px;top:56px">2020</div><p class="tx light xs" style="left:26px;top:62px;width:42px;text-align:left">Managed support and secure cloud for growing enterprise teams.</p>
  <div class="abs" style="left:13px;top:92px;font:500 10px/1.2 'Poppins',sans-serif;color:var(--white)">For<br><b>2 Years</b></div>
  <div class="logo">travolin</div>
  <svg class="abs" style="left:78px;top:15px" width="162" height="110" viewBox="0 0 162 110" fill="none">
    <path d="M60 60 V95 Q60 108 80 110 H140" stroke="#29b5ec" stroke-width="1"/>
    <path d="M70 55 Q60 40 48 40 Q40 40 40 32 Q40 22 30 22 M30 22 Q20 22 20 12" stroke="#29b5ec" stroke-width=".8"/>
    <path d="M140 80 V108" stroke="#1c2540" stroke-dasharray="1 1.5" stroke-width=".8"/>
    <g stroke="#1c2540" stroke-width="1.6" fill="#fff">
      <circle cx="140" cy="62" r="15"/><circle cx="74" cy="55" r="9"/><circle cx="110" cy="38" r="7"/><circle cx="45" cy="33" r="5"/><circle cx="63" cy="20" r="4"/><circle cx="30" cy="13" r="3"/>
    </g>
    <g fill="#29b5ec" font-family="Poppins,sans-serif" font-weight="700" text-anchor="middle">
      <text x="140" y="69" font-size="18">1</text><text x="74" y="59" font-size="11">2</text><text x="110" y="42" font-size="9">3</text><text x="45" y="35" font-size="6">4</text><text x="63" y="22" font-size="5">5</text><text x="30" y="15" font-size="3.5">6</text>
    </g>
  </svg>
  <div class="head cyan" style="left:104px;top:10px;font-size:3.4px">Lorem Ipsum</div><p class="tx xs" style="left:104px;top:15px;width:28px;text-align:left">Managed support for growing enterprise teams.</p>
  <div class="head cyan" style="left:148px;top:22px;font-size:3.4px">Lorem Ipsum</div><p class="tx xs" style="left:148px;top:27px;width:28px;text-align:left">Managed support for growing enterprise teams.</p>
  <div class="head cyan" style="left:199px;top:24px;font-size:3.4px">Lorem Ipsum</div><p class="tx xs" style="left:199px;top:29px;width:28px;text-align:left">Managed support for growing enterprise teams.</p>
  <div class="head cyan" style="left:115px;top:82px;font-size:3.4px">Lorem Ipsum</div><p class="tx xs" style="left:115px;top:87px;width:28px;text-align:left">Managed support for growing enterprise teams.</p>
  <div class="head cyan" style="left:190px;top:98px;font-size:3.4px">Lorem Ipsum</div><p class="tx xs" style="left:190px;top:103px;width:28px;text-align:left">Managed support for growing enterprise teams.</p>
  <div class="foot light"><b>www</b>travolin.com.au</div><div class="pg"></div>
</section>

<!-- 20 costs -->
<section class="slide">
  <div class="panel" style="left:0;top:0;right:0;height:43px"></div>
  <div class="title light" style="left:9px;top:6px">Company Costs</div>
  <div class="logo">travolin</div>
  <p class="tx light" style="left:10px;top:21px;width:218px">Secure cloud and managed services for enterprise teams across Australia and the region. We plan, migrate and protect critical systems so your people can focus on growth. Our engineers watch networks around the clock and respond fast. Secure cloud and managed services for enterprise teams across Australia and the region. We plan, migrate and protect critical systems so your people can focus on growth.</p>
  <svg class="abs" style="left:10px;top:50px" width="220" height="32" viewBox="0 0 220 32">
    <rect x="4" y="26" width="200" height="4" fill="#29b5ec"/>
    <rect x="90" y="26" width="118" height="4" fill="#1c2540"/>
    <path d="M208 24 L216 28 L208 32 Z" fill="#1c2540"/>
    <g fill="none" stroke-width="4"><circle cx="40" cy="14" r="11" stroke="#29b5ec"/><circle cx="82" cy="14" r="11" stroke="#1c2540"/><circle cx="124" cy="14" r="11" stroke="#29b5ec"/><circle cx="166" cy="14" r="11" stroke="#1c2540"/></g>
    <g fill="none" stroke="#1c2540" stroke-width=".8"><circle cx="40" cy="14" r="4"/><path d="M40 11 V14 H42"/><circle cx="82" cy="14" r="4" fill="#29b5ec" stroke="none"/><ellipse cx="124" cy="11" rx="4" ry="1.5"/><path d="M120 11 V17 Q124 19 128 17 V11"/><circle cx="165" cy="13" r="3"/><path d="M167 15 L170 18"/></g>
    <g font-family="Poppins,sans-serif" font-size="3" fill="#fff" font-weight="600"><text x="54" y="29.3">Step 01</text><text x="96" y="29.3">Step 02</text><text x="138" y="29.3">Step 03</text><text x="180" y="29.3">Step 04</text></g>
  </svg>
  <div class="head" style="left:35px;top:90px;width:30px;text-align:center">Lorem Ipsum</div><p class="tx xs c" style="left:33px;top:96px;width:34px">Managed support and secure cloud for growing enterprise teams.</p>
  <div class="head cyan" style="left:77px;top:90px;width:30px;text-align:center">Lorem Ipsum</div><p class="tx xs c" style="left:75px;top:96px;width:34px">Managed support and secure cloud for growing enterprise teams.</p>
  <div class="head" style="left:119px;top:90px;width:30px;text-align:center">Lorem Ipsum</div><p class="tx xs c" style="left:117px;top:96px;width:34px">Managed support and secure cloud for growing enterprise teams.</p>
  <div class="head cyan" style="left:161px;top:90px;width:30px;text-align:center">Lorem Ipsum</div><p class="tx xs c" style="left:159px;top:96px;width:34px">Managed support and secure cloud for growing enterprise teams.</p>
  <div class="foot"><b>www</b>travolin.com.au</div><div class="pg"></div>
</section>

<!-- 21 timeline -->
<section class="slide">
  <div class="title" style="left:9px;top:6px">Company Timeline</div>
  <div class="logo">travolin</div>
  <svg class="abs" style="left:25px;top:48px" width="205" height="50" viewBox="0 0 205 50" font-family="Poppins,sans-serif" font-weight="600" font-size="5.5" text-anchor="middle">
    <path d="M0 6 H180 Q196 6 196 22 Q196 38 180 38 H0" fill="none" stroke="#29b5ec" stroke-width=".8"/>
    <path d="M0 6 H8" stroke="#1c2540" stroke-dasharray="2 1" stroke-width=".8"/>
    <g fill="#fff" stroke="#1c2540" stroke-width=".8"><circle cx="20" cy="6" r="1.8"/><circle cx="45" cy="6" r="1.8"/><circle cx="70" cy="6" r="1.8"/><circle cx="95" cy="6" r="1.8"/><circle cx="120" cy="6" r="1.8"/><circle cx="145" cy="6" r="1.8"/><circle cx="20" cy="38" r="1.8"/><circle cx="45" cy="38" r="1.8"/><circle cx="70" cy="38" r="1.8"/><circle cx="95" cy="38" r="1.8"/><circle cx="120" cy="38" r="1.8"/><circle cx="145" cy="38" r="1.8"/></g>
    <text x="20" y="15" fill="#29b5ec">Jan</text><text x="45" y="15" fill="#1c2540">Feb</text><text x="70" y="15" fill="#29b5ec">Mar</text><text x="95" y="15" fill="#1c2540">Apr</text><text x="120" y="15" fill="#29b5ec">May</text><text x="145" y="15" fill="#1c2540">Jun</text>
    <text x="20" y="33" fill="#29b5ec">Dec</text><text x="45" y="33" fill="#1c2540">Nov</text><text x="70" y="33" fill="#29b5ec">Oct</text><text x="95" y="33" fill="#1c2540">Sep</text><text x="120" y="33" fill="#29b5ec">Aug</text><text x="145" y="33" fill="#1c2540">Jul</text>
  </svg>
  <div class="abs" style="left:42px;top:26px;display:grid;grid-template-columns:repeat(6,25px)">
    <div><div class="head" style="position:static">01</div><p class="tx xs" style="position:static;width:21px;text-align:left">Support for growing teams.</p></div>
    <div><div class="head" style="position:static">02</div><p class="tx xs" style="position:static;width:21px;text-align:left">Support for growing teams.</p></div>
    <div><div class="head" style="position:static">03</div><p class="tx xs" style="position:static;width:21px;text-align:left">Support for growing teams.</p></div>
    <div><div class="head" style="position:static">04</div><p class="tx xs" style="position:static;width:21px;text-align:left">Support for growing teams.</p></div>
    <div><div class="head" style="position:static">05</div><p class="tx xs" style="position:static;width:21px;text-align:left">Support for growing teams.</p></div>
    <div><div class="head" style="position:static">06</div><p class="tx xs" style="position:static;width:21px;text-align:left">Support for growing teams.</p></div>
  </div>
  <div class="abs" style="left:42px;top:98px;display:grid;grid-template-columns:repeat(6,25px)">
    <div><div class="head" style="position:static">12</div><p class="tx xs" style="position:static;width:21px;text-align:left">Support for growing teams.</p></div>
    <div><div class="head" style="position:static">11</div><p class="tx xs" style="position:static;width:21px;text-align:left">Support for growing teams.</p></div>
    <div><div class="head" style="position:static">10</div><p class="tx xs" style="position:static;width:21px;text-align:left">Support for growing teams.</p></div>
    <div><div class="head" style="position:static">09</div><p class="tx xs" style="position:static;width:21px;text-align:left">Support for growing teams.</p></div>
    <div><div class="head" style="position:static">08</div><p class="tx xs" style="position:static;width:21px;text-align:left">Support for growing teams.</p></div>
    <div><div class="head" style="position:static">07</div><p class="tx xs" style="position:static;width:21px;text-align:left">Support for growing teams.</p></div>
  </div>
  <div class="foot"><b>www</b>travolin.com.au</div><div class="pg"></div>
</section>

<!-- 22 text here phones -->
<section class="slide">
  <div class="title" style="left:7px;top:9px">Text Here</div>
  <div class="logo">travolin</div>
  <p class="tx" style="left:7px;top:26px;width:80px">Secure cloud and managed services for enterprise teams across Australia and the region. We plan, migrate and protect critical systems so your people can focus on growth. Our engineers watch networks around the clock and respond fast.</p>
  <p class="tx" style="left:7px;top:52px;width:80px">Secure cloud and managed services for enterprise teams, with round-the-clock monitoring and fast local support.</p>
  <div class="panel" style="left:0;top:72px;width:77px;height:46px"></div>
  <div class="num" style="left:11px;top:75px;width:7px;height:7px;border-radius:0;line-height:7px;font-size:4px">1</div>
  <div class="head cyan" style="left:21px;top:75px;font-size:3.2px">Lorem ipsum</div><p class="tx light xs" style="left:21px;top:79px;width:52px;text-align:left">Managed support and secure cloud for growing enterprise teams.</p>
  <div class="num" style="left:11px;top:89px;width:7px;height:7px;border-radius:0;line-height:7px;font-size:4px">2</div>
  <div class="head cyan" style="left:21px;top:89px;font-size:3.2px">Lorem ipsum</div><p class="tx light xs" style="left:21px;top:93px;width:52px;text-align:left">Managed support and secure cloud for growing enterprise teams.</p>
  <div class="num" style="left:11px;top:103px;width:7px;height:7px;border-radius:0;line-height:7px;font-size:4px">3</div>
  <div class="head cyan" style="left:21px;top:103px;font-size:3.2px">Lorem ipsum</div><p class="tx light xs" style="left:21px;top:107px;width:52px;text-align:left">Managed support and secure cloud for growing enterprise teams.</p>
  <div class="abs" style="left:95px;top:28px;width:140px;height:80px;background:radial-gradient(ellipse at center,#e8ecf2,#fff 70%)" role="img" aria-label="Faint world map"></div>
  <div class="abs" style="left:99px;top:17px;width:28px;height:58px;border:1.4px solid var(--navy);border-radius:4px;background:var(--white);padding:6px 3px">
    <div style="font:500 3.6px/1.1 'Poppins',sans-serif;color:var(--navy)">Lorem ipsum dolor</div>
    <p class="tx xs" style="position:static;margin-top:12px;text-align:left">Managed support and secure cloud for growing enterprise teams.</p>
  </div>
  <div class="abs" style="left:136px;top:40px;width:28px;height:58px;border:1.4px solid var(--navy);border-radius:4px;background:var(--white);padding:6px 3px">
    <div style="font:500 3.6px/1.1 'Poppins',sans-serif;color:var(--navy)">Dolor sit amet, conse</div>
    <p class="tx xs" style="position:static;margin-top:12px;text-align:left">Managed support and secure cloud for growing enterprise teams.</p>
  </div>
  <div class="abs" style="left:172px;top:62px;width:28px;height:58px;border:1.4px solid var(--navy);border-radius:4px;background:var(--white);padding:6px 3px">
    <div style="font:500 3.6px/1.1 'Poppins',sans-serif;color:var(--navy)">Consec</div>
    <p class="tx xs" style="position:static;margin-top:12px;text-align:left">Managed support and secure cloud for growing enterprise teams.</p>
  </div>
  <div class="foot"><b>www</b>travolin.com.au</div><div class="pg"></div>
</section>

<!-- 23 team -->
<section class="slide">
  <div class="title" style="left:7px;top:9px">Our Team</div>
  <div class="logo">travolin</div>
  <p class="tx" style="left:7px;top:24px;width:226px">Secure cloud and managed services for enterprise teams across Australia and the region. We plan, migrate and protect critical systems so your people can focus on growth. Our engineers watch networks around the clock and respond fast.</p>
  <p class="tx" style="left:7px;top:38px;width:226px">Secure cloud and managed services for enterprise teams across Australia and the region. We plan, migrate and protect critical systems so your people can focus on growth. Our engineers watch networks around the clock and respond fast.</p>
  <div class="panel" style="left:0;top:67px;right:0;height:50px"></div>
  <div class="abs" style="left:0;top:56px;width:240px;display:grid;grid-template-columns:repeat(4,1fr);text-align:center">
    <div><div style="width:21px;height:21px;border-radius:50%;margin:0 auto;background:linear-gradient(#dfe4ea,#a7b1bf);border:1px solid var(--white)" role="img" aria-label="Team member portrait"></div><div style="font:700 4px 'Poppins',sans-serif;color:var(--cyan);margin-top:3px">ARAN PIKE</div><p class="tx light xs c" style="position:static;width:36px;margin:1px auto 0">Managed support and secure cloud for growing enterprise teams.</p></div>
    <div><div style="width:21px;height:21px;border-radius:50%;margin:0 auto;background:linear-gradient(#dfe4ea,#a7b1bf);border:1px solid var(--white)" role="img" aria-label="Team member portrait"></div><div style="font:700 4px 'Poppins',sans-serif;color:var(--cyan);margin-top:3px">LEAH MOSS</div><p class="tx light xs c" style="position:static;width:36px;margin:1px auto 0">Managed support and secure cloud for growing enterprise teams.</p></div>
    <div><div style="width:21px;height:21px;border-radius:50%;margin:0 auto;background:linear-gradient(#dfe4ea,#a7b1bf);border:1px solid var(--white)" role="img" aria-label="Team member portrait"></div><div style="font:700 4px 'Poppins',sans-serif;color:var(--cyan);margin-top:3px">ARAN PIKE</div><p class="tx light xs c" style="position:static;width:36px;margin:1px auto 0">Managed support and secure cloud for growing enterprise teams.</p></div>
    <div><div style="width:21px;height:21px;border-radius:50%;margin:0 auto;background:linear-gradient(#dfe4ea,#a7b1bf);border:1px solid var(--white)" role="img" aria-label="Team member portrait"></div><div style="font:700 4px 'Poppins',sans-serif;color:var(--cyan);margin-top:3px">LEAH MOSS</div><p class="tx light xs c" style="position:static;width:36px;margin:1px auto 0">Managed support and secure cloud for growing enterprise teams.</p></div>
  </div>
  <div class="foot"><b>www</b>travolin.com.au</div><div class="pg"></div>
</section>

<!-- 24 thank you -->
<section class="slide">
  <div class="abs" style="left:4px;top:3px;width:5px;height:5px;background:var(--cyan)"></div>
  <div class="abs" style="left:0;right:0;top:10px;text-align:center;font:700 19px 'Poppins',sans-serif;color:var(--navy);letter-spacing:.5px">Thank You</div>
  <div class="panel" style="left:0;right:0;top:42px;height:57px;background:linear-gradient(180deg,#1c2540,#23315a)"></div>
  <div class="abs" style="left:0;right:0;top:50px;text-align:center;font:300 26px 'Poppins',sans-serif;color:var(--cyan)">travolin</div>
  <div class="abs" style="left:63px;top:108px;font:500 8px 'Poppins',sans-serif;color:var(--navy)">Contact Us</div>
  <div class="abs" style="left:114px;top:106px;font:400 4.2px/1.6 'Poppins',sans-serif;color:var(--navy)">
    <div><span style="color:var(--cyan)">●</span> 0400 555 210</div>
    <div><span style="color:var(--cyan)">●</span> hello@travolin-mail.com</div>
  </div>
</section>

</main>
</body>
</html>
```